VL - menu design

Hi,

We require elegant menu design for upscale restaurant. Please find attached the logo and the menu items for your reference.

for inspiration, this is a good website: -
http://www.plateworthy-sample.net/dishcraft/about.php

We are very much open for Menu Size suggestions.

unfortunately the place is going under renovation, we don't have updated images to it. the closest look and feel to our place is http://vazelo-example.com ..

we are also open for creative options on the shape, the styles, etc. as long as it represents the fine dine feel ...

Thanks ...

Dear All,

We wouldlike to extend our apology for not being able to provide feedbacks on everysingle design. We were extremely busy and we have multiple contests opensimultaneously which makes the process even harder.

However,we would like to thank you all for the efforts you have put into designingour menu. It is very much appreciated …

We wishyou all success in your design ventures and we are quite positive that we willbe working with many of you on many projects in the soon future. 

Thanks & Regards,

DQI Team...

 

 

 

Industry/Entity Type

Restaurant

Requirements
Must have
• Please ensure that there are 'some' images in the menu ... this is very important.
Should not have
• IMPORTANT: -

1. Please DO NOT insert any currency sign to the menu
2. Please keep the prices of the menu at the end of the menu items descriptions NOT beside the menu item names. The font of the price should be similar to the menu item description and please DO NOT bold the numbers. the prices should be subtle.

Thank you ...

```html
<!DOCTYPE html>
<html lang="en">
<head>
<meta charset="utf-8">
<title>Quince Cafe – Menu</title>
<link href="https://fonts.googleapis.com/css2?family=Saira:wght@300;400&family=Crimson+Text:ital,wght@0,400;0,700;1,400;1,700&display=swap" rel="stylesheet">
<style>
  :root {
    --backdrop: #d9d9d6;
    --paper: #ffffff;
    --ink: #222222;
    --ink-soft: #3a3a3a;
    --rule: #9a9a9a;
    --logo-block: #2b2b2b;
    --logo-text: #f4f4f4;
    --accent: #9c7f55;
    --heading: #4a4a4a;
    --art-warm: #d9ccb5;
    --art-cool: #c9bda6;
  }
  * { box-sizing: border-box; margin: 0; padding: 0; }
  html, body { width: 1200px; height: 801px; overflow: hidden; background: var(--backdrop); }
  .menu-page {
    position: absolute; left: 215px; top: 8px; width: 770px; height: 785px;
    background: var(--paper); color: var(--ink);
    font-family: "Crimson Text", Georgia, serif;
  }
  .brand-block {
    position: absolute; left: 0; top: 0; width: 280px; height: 103px;
    background: var(--logo-block); display: flex; align-items: center; justify-content: center;
  }
  .brand-name {
    font-family: "Saira", Arial, sans-serif; font-weight: 300; font-size: 26px;
    letter-spacing: 5px; color: var(--logo-text); text-transform: uppercase;
  }
  .hero-art {
    position: absolute; left: 381px; top: 13px; width: 172px; height: 94px;
    background: radial-gradient(ellipse at center, var(--art-cool) 0%, var(--art-warm) 55%, var(--paper) 75%);
  }
  .side-art {
    position: absolute; left: 75px; top: 690px; width: 140px; height: 70px;
    background: radial-gradient(ellipse at center, var(--art-cool) 0%, var(--art-warm) 50%, var(--paper) 75%);
  }
  .column-divider { position: absolute; left: 295px; top: 125px; width: 1px; height: 635px; background: var(--rule); }
  .section { position: absolute; }
  .section-title {
    font-family: "Saira", Arial, sans-serif; font-weight: 300; font-size: 21px;
    letter-spacing: 1.5px; color: var(--heading); text-transform: uppercase; text-align: center;
    border-top: 1px solid var(--rule); padding-top: 4px; margin-bottom: 8px; line-height: 1.1;
  }
  .dish { text-align: center; font-size: 9.6px; line-height: 11.6px; margin-bottom: 6px; }
  .dish-name { font-style: italic; font-weight: 700; }
  .dish-desc { font-style: italic; color: var(--ink-soft); }
  .first-courses { left: 306px; top: 124px; width: 460px; }
  .first-courses .dish { margin-bottom: 5px; font-size: 10px; }
  .appetizers { left: 17px; top: 212px; width: 268px; }
  .appetizers .dish { margin-bottom: 9px; }
  .main-courses { left: 306px; top: 410px; width: 214px; }
  .rotisserie { left: 531px; top: 410px; width: 235px; }
  .rotisserie .dish-title {
    display: block; color: var(--accent); font-weight: 700; font-size: 11px; margin-bottom: 1px;
  }
  .rotisserie .dish { margin-bottom: 5px; }
</style>
</head>
<body>
<main class="menu-page">
  <header class="brand-block"><span class="brand-name">Quince Cafe</span></header>
  <div class="hero-art" role="img" aria-label="Engraved illustration of a roast chicken"></div>

  <section class="section first-courses">
    <h2 class="section-title">First Courses</h2>
    <p class="dish"><span class="dish-name">Tagliatelle served on a whole Lobster</span> <span class="dish-desc">with fresh Asparagus tips, cherry tomato and crispy beef bacon. 249</span></p>
    <p class="dish"><span class="dish-name">Whole wheat Maltagliati</span> <span class="dish-desc">with Porcini mushrooms and Parmesan cheese cream. 99</span></p>
    <p class="dish"><span class="dish-name">Penne pasta with fresh broccoli,</span> <span class="dish-desc">Taleggio cheese cream, toasted almonds and fresh chili</span></p>
    <p class="dish"><span class="dish-name">Spaghetti</span> <span class="dish-desc">with a smooth and creamy sauce and juicy chicken breast</span></p>
    <p class="dish"><span class="dish-name">Fettuccine with fresh salmon,</span> <span class="dish-desc">saffron and toasted pine nuts</span></p>
    <p class="dish"><span class="dish-name">Seasoned tagliatelle</span> <span class="dish-desc">with king scallops and poached egg</span></p>
    <p class="dish"><span class="dish-name">Risotto with Prawns,</span> <span class="dish-desc">green peas and beetroot reduction. 149</span></p>
    <p class="dish"><span class="dish-name">Risotto "Primavera"</span> <span class="dish-desc">with fresh seasoned vegetables served on a squash cream. 69</span></p>
    <p class="dish"><span class="dish-name">Risotto with porcini mushrooms</span> <span class="dish-desc">and garlic chips</span></p>
  </section>

  <div class="column-divider"></div>

  <section class="section appetizers">
    <h2 class="section-title">Appetizers</h2>
    <p class="dish"><span class="dish-name">Fresh tomato and mozzarella</span> <span class="dish-desc">terrine with basil cream, black olives and fresh capers.</span></p>
    <p class="dish"><span class="dish-name">Fresh salmon sashimi</span> <span class="dish-desc">seared in olive oil with spring and red onions, orange zest and fresh sweet chilli 79</span></p>
    <p class="dish"><span class="dish-name">Duck Foie Gras</span> <span class="dish-desc">terrine with toasted Pan Brioche and red onion jam glaze. 124</span></p>
    <p class="dish"><span class="dish-name">Selection of vegetables</span> <span class="dish-desc">stuffed with fresh spinach, goat cheese and fresh mint on a garlic-tomato coulis. 97</span></p>
    <p class="dish"><span class="dish-name">Grilled Octopus</span> <span class="dish-desc">with bell peppers, roasted tofu, lemon zest and sweet n' sour soy drops. 99</span></p>
    <p class="dish"><span class="dish-name">Sea Scallops "au gratin"</span> <span class="dish-desc">with garlic chips, seafood cream and truffle oil. 174</span></p>
    <p class="dish"><span class="dish-name">Irish Beef "Carpaccio"</span> <span class="dish-desc">on a Reggiano cheese sauce and truffle slices, with toasted pine nuts and seasonal fresh salad. 79</span></p>
    <p class="dish"><span class="dish-name">Prawns</span> <span class="dish-desc">with white chocolate sauce, thyme creamy, fresh celery on a Vinaigrette potato cream. 69</span></p>
  </section>
  <div class="side-art" role="img" aria-label="Engraved illustration of a seafood dish"></div>

  <section class="section main-courses">
    <h2 class="section-title">Main Courses</h2>
    <p class="dish"><span class="dish-name">Grilled beef tenderloin</span> <span class="dish-desc">with balsamic sauce, mashed potatoes and grilled pumpkin. 149</span></p>
    <p class="dish"><span class="dish-name">Chicken supreme</span> <span class="dish-desc">stuffed with Fontina cheese, spinach and black olives in a crispy panko crust served on aubergine "Caponata". 139</span></p>
    <p class="dish"><span class="dish-name">Grilled fresh Salmon</span> <span class="dish-desc">dusted in herbs with seasoned roasted vegetables with sesame and light soy sauce. 149</span></p>
    <p class="dish"><span class="dish-name">Sea Bass</span> <span class="dish-desc">crumble with smashed potato and Zucchini ratatouille. 159</span></p>
    <p class="dish"><span class="dish-name">The Paella,</span> <span class="dish-desc">traditional Spanish seafood and chicken dish, served with saffron rice and green peas. 229</span></p>
    <p class="dish"><span class="dish-name">Stuffed calamari</span> <span class="dish-desc">with breadcrumbs, black olives, green peas served on a semolina cream and fresh tomato sauce.</span></p>
  </section>

  <section class="section rotisserie">
    <h2 class="section-title">The Rotisserie</h2>
    <p class="dish"><span class="dish-title">Spring chicken</span><span class="dish-desc">Marinated in fresh rosemary, lemon zest, garlic and black pepper grains served with baked potatoes, herb butter, sage rice and our lemon pickle sauce. 139</span></p>
    <p class="dish"><span class="dish-title">Baby Duck</span><span class="dish-desc">Roasted in Banana leaves and fresh lemongrass served with potatoes "au gratin", sautéed Foie Gras slices, red onion rings and toasted orange sauce. 149</span></p>
    <p class="dish"><span class="dish-title">Boneless Lamb</span><span class="dish-desc">Stuffed with black olives and dried plums, served on smashed fresh spinach, toasted pine nuts, garlic breadcrumbs and thyme mashed potatoes. 149</span></p>
    <p class="dish"><span class="dish-title">Beef Sirloin</span><span class="dish-desc">Marinated in spring onions, garlic and mustard, served on rosemary potatoes, Vichy carrots and green pepper sauce. 149</span></p>
    <p class="dish"><span class="dish-title">Chicken Shawarma</span><span class="dish-desc">Served in the inimitable Quince style with garlic sauce, cucumber and tomato pickles and three peppers coulis. 72</span></p>
  </section>
</main>
</body>
</html>
```